Every Shelf Set Neatly or ESN Organized needs a business card design. ESN Organized is a professi

We need a business card design that is clean, sharp and conveys a sense of organization. I already have a logo.

Target Market(s)

Families (specifically mothers), small business owners, parents, seniors

Industry/Entity Type

Business

Contact Information for Business Card

My website is www.esnorganized-example.com and my Facebook page is http://www.sociallink-example.com/everyshelfsetneatly. The phone number is 418-552-7094 and I want to be listed as Lorna M. Pelham, Owner

Requirements
Must have
• My logo.

```html
<!DOCTYPE html>
<html lang="en">
<head>
<meta charset="utf-8">
<title>ESN Organized – Business Card</title>
<link rel="stylesheet" href="https://fonts.googleapis.com/css2?family=Open+Sans:wght@400;600&display=swap">
<style>
  :root {
    --canvas: #eceae7;
    --card-blue: #0a7bd8;
    --card-white: #ffffff;
    --text-light: #ffffff;
    --brand-ink: #1f6fc4;
    --clip-tone-a: #ffffff;
    --clip-tone-b: #d6e8f8;
  }
  * { margin: 0; padding: 0; box-sizing: border-box; }
  html, body {
    width: 1200px; height: 900px; overflow: hidden;
    background: var(--canvas);
    font-family: "Open Sans", Arial, sans-serif;
  }
  .canvas { position: relative; width: 1200px; height: 900px; }

  .card { position: absolute; width: 556px; height: 343px; box-shadow: 0 4px 14px rgba(0,0,0,.12); }

  /* Front */
  .card-front { left: 238px; top: 62px; background: var(--card-blue); color: var(--text-light); }
  .card-front .feature-art {
    position: absolute; right: 0; top: 0; width: 176px; height: 100%;
    background: linear-gradient(90deg, var(--clip-tone-b), var(--clip-tone-a) 35%);
  }
  .holder { position: absolute; left: 38px; top: 62px; }
  .holder-name { font-size: 18px; font-weight: 600; line-height: 1.2; }
  .holder-title { font-size: 14px; font-weight: 400; line-height: 1.2; }

  .contact-list { position: absolute; left: 32px; top: 191px; list-style: none; }
  .contact-list li { display: flex; align-items: center; gap: 7px; font-size: 15px; height: 20px; }
  .contact-list svg { width: 13px; height: 13px; fill: var(--text-light); flex: none; }
  .social-link { position: absolute; left: 32px; top: 277px; font-size: 15px; }

  /* Back */
  .card-back { left: 457px; top: 519px; width: 560px; background: var(--card-white); }
  .brand-name {
    position: absolute; left: 0; right: 0; top: 150px; text-align: center;
    font-size: 34px; font-weight: 400; letter-spacing: 5px;
    color: var(--brand-ink);
  }
</style>
</head>
<body>
<main class="canvas">

  <section class="card card-front" aria-label="Business card front">
    <div class="feature-art" role="img" aria-label="Large decorative brand symbol in blue on white"></div>

    <div class="holder">
      <p class="holder-name">Lorna M. Pelham</p>
      <p class="holder-title">Owner</p>
    </div>

    <ul class="contact-list">
      <li>
        <svg viewBox="0 0 24 24" aria-hidden="true"><path d="M6.6 10.8a15 15 0 0 0 6.6 6.6l2.2-2.2c.3-.3.7-.4 1-.2 1.1.4 2.3.6 3.6.6.6 0 1 .4 1 1V20c0 .6-.4 1-1 1A17 17 0 0 1 3 4c0-.6.4-1 1-1h3.5c.6 0 1 .4 1 1 0 1.3.2 2.5.6 3.6.1.3 0 .7-.2 1z"/></svg>
        418-552-7094
      </li>
      <li>
        <svg viewBox="0 0 24 24" aria-hidden="true"><path d="M3 6h18v12H3z M3 6l9 7 9-7" fill="none" stroke="#fff" stroke-width="0"/><path d="M3 6h18l-9 7z M3 8l9 7 9-7v10H3z"/></svg>
        info@esnorganized-example.com
      </li>
      <li>
        <svg viewBox="0 0 24 24" aria-hidden="true"><circle cx="12" cy="12" r="10"/><path d="M2 12h20M12 2c3 3 3 17 0 20M12 2c-3 3-3 17 0 20" stroke="#0a7bd8" stroke-width="1.6" fill="none"/></svg>
        www.esnorganized-example.com
      </li>
    </ul>

    <p class="social-link">www.sociallink-example.com/everyshelfsetneatly</p>
  </section>

  <section class="card card-back" aria-label="Business card back">
    <p class="brand-name">ESN Organized</p>
  </section>

</main>
</body>
</html>
```